Web design

We need the design for the logo and website for a women fashion website. No coding required. The colors used should be neutral (maybe with a light touch of color), the style should be modern, slightly luxurious, not too crowded. The target market is young professionals who love trendy clothes.
Updates

Need extra days to review

Target Market(s)

Young professionals

Industry/Entity Type

Apparel

Number of Pages Required

5+ page

Font styles to use
Sans Serif
Other font styles liked:
• Montserrat, Engravers Gothic, Benton Sans, gotham-book

Colors

Designer to choose colors to be used in the design.

```html
<!DOCTYPE html>
<html lang="en">
<head>
<meta charset="utf-8">
<title>LUNE – Access your account</title>
<link href="https://fonts.googleapis.com/css2?family=Montserrat:wght@400;500;600;700&display=swap" rel="stylesheet">
<style>
:root{
  --ink:#1f1f1f;
  --text:#555;
  --muted:#a9a9a9;
  --faint:#c8c8c8;
  --line:#cfcfcf;
  --sale:#d9453c;
  --band:#f3f3f3;
  --white:#fff;
}
*{box-sizing:border-box;margin:0;padding:0}
html,body{width:849px;height:1200px;overflow:hidden;background:var(--white)}
body{font-family:"Montserrat",sans-serif;color:var(--text);font-size:7px;line-height:1.6;position:relative}
a{color:inherit;text-decoration:none}

/* header */
.site-header{position:absolute;top:0;left:0;width:849px;height:60px;display:flex;align-items:center;padding:0 30px;border-bottom:1px solid #eee}
.main-nav{display:flex;gap:22px;font-size:8px;color:var(--ink);font-weight:500}
.main-nav .sale{color:var(--sale)}
.brand{position:absolute;left:50%;transform:translateX(-50%)}
.brand-name{font-size:24px;font-weight:500;letter-spacing:2px;color:var(--ink)}
.header-tools{margin-left:auto;display:flex;gap:12px;align-items:center;font-size:7px;color:var(--ink)}

/* breadcrumb + sidebar */
.breadcrumb{position:absolute;top:120px;left:70px;font-size:7px;color:var(--ink)}
.account-menu{position:absolute;top:158px;left:70px;width:250px}
.menu-item{display:flex;gap:12px;margin-bottom:30px;color:var(--faint)}
.menu-item svg{flex:none;margin-top:1px}
.menu-item h4{font-size:7.5px;font-weight:600;text-transform:uppercase;margin-bottom:2px}
.menu-item p{font-size:6px;line-height:1.5}
.menu-item.active{color:var(--ink)}
.menu-item.active p{color:var(--text)}

/* account panel */
.account-panel{position:absolute;top:118px;left:348px;width:430px}
.panel-title{font-size:10.5px;font-weight:600;color:var(--ink);text-transform:uppercase;margin-bottom:12px}
.section-title{font-size:13px;font-weight:500;color:var(--ink);text-transform:uppercase;margin-bottom:12px}
.field-row{display:flex;justify-content:space-between;align-items:baseline}
.field-label{font-size:7.5px;font-weight:600;color:var(--ink);text-transform:uppercase}
.field-action{font-size:6.5px;color:var(--ink)}
.field-action::after{content:" ✎";font-size:7px}
.divider{border:0;border-top:1px dashed var(--line);margin:24px 0}
.divider.solid{border-top:1.5px solid var(--ink)}
.block p{margin-top:6px}
.sub-label{font-size:7.5px;font-weight:600;color:var(--ink);margin-top:18px}
.choices{display:flex;gap:14px;margin-top:20px;font-size:6.5px;font-weight:600;color:var(--ink);text-transform:uppercase}
.choice{display:flex;align-items:center;gap:4px}
.box{width:8px;height:8px;border:1px solid var(--ink);display:inline-block}
.strong{font-weight:600;color:var(--ink)}
.billing p{margin-top:3px}
.store-form{display:flex;gap:10px;margin-top:18px}
.store-form .input{height:18px;border:1px solid var(--line);font-size:6.5px;color:var(--muted);padding:0 8px;display:flex;align-items:center;justify-content:space-between}
.input.county{width:135px}
.input.city{width:135px}
.search-btn{width:110px;height:18px;border:1px solid var(--ink);font-size:6.5px;font-weight:600;color:var(--ink);display:flex;align-items:center;justify-content:center}

/* footer */
.site-footer{position:absolute;top:1000px;left:0;width:849px;height:200px;background:var(--band)}
.footer-brand{position:absolute;left:70px;top:28px}
.footer-brand .brand-name{font-size:28px}
.footer-col{position:absolute;top:32px}
.footer-col h5{font-size:9px;font-weight:600;color:var(--ink);margin-bottom:8px}
.footer-col li{list-style:none;font-size:6.5px;line-height:2}
.col-help{left:311px}
.col-shop{left:515px}
.col-contact{left:679px}
.socials{display:flex;gap:5px;margin-top:4px}
.socials span{width:13px;height:13px;border:1px solid var(--ink);border-radius:50%}
.footer-base{position:absolute;left:70px;right:70px;top:150px;border-top:1px solid var(--line);padding-top:8px;text-align:center;font-size:6.5px}
</style>
</head>
<body>

<header class="site-header">
  <nav class="main-nav">
    <a>Latest Arrivals</a><a>Clothes ▾</a><a>LUNE Club</a><a class="sale">On Sale</a>
  </nav>
  <div class="brand"><span class="brand-name">LUNE</span></div>
  <div class="header-tools">
    <svg width="10" height="10" viewBox="0 0 10 10" fill="none" stroke="#1f1f1f"><circle cx="4.2" cy="4.2" r="3.2"/><path d="M6.6 6.6 9.3 9.3"/></svg>
    <span>RON ▾</span>
    <svg width="11" height="10" viewBox="0 0 11 10" fill="none" stroke="#1f1f1f"><path d="M5.5 9 1.3 4.8A2.4 2.4 0 0 1 5.5 1.8a2.4 2.4 0 0 1 4.2 3Z"/></svg>
    <svg width="10" height="10" viewBox="0 0 10 10" fill="none" stroke="#1f1f1f"><circle cx="5" cy="3" r="2.2"/><path d="M1 9.5a4 4 0 0 1 8 0"/></svg>
    <svg width="10" height="10" viewBox="0 0 10 10" fill="none" stroke="#1f1f1f"><path d="M1.5 3.5h7l-.6 6H2.1Z"/><path d="M3.5 3.5a1.5 1.5 0 0 1 3 0"/></svg>
  </div>
</header>

<div class="breadcrumb">My account / Access your account</div>

<aside class="account-menu">
  <div class="menu-item active">
    <svg width="12" height="14" viewBox="0 0 12 14" fill="none" stroke="currentColor"><rect x="1" y="6" width="10" height="7"/><path d="M3 6V4a3 3 0 0 1 6 0v2"/></svg>
    <div><h4>Access your account</h4><p>From here you will be able to change the password and e-mail address used to access your account.</p></div>
  </div>
  <div class="menu-item">
    <svg width="12" height="14" viewBox="0 0 12 14" fill="none" stroke="currentColor"><circle cx="6" cy="4" r="3"/><path d="M1 13a5 5 0 0 1 10 0"/></svg>
    <div><h4>Personal data</h4><p>Review and update your name, billing details and phone number whenever you need to.</p></div>
  </div>
  <div class="menu-item">
    <svg width="12" height="14" viewBox="0 0 12 14" fill="none" stroke="currentColor"><rect x="1" y="3" width="10" height="10"/><path d="M1 6h10"/></svg>
    <div><h4>Orders</h4><p>You can check the status of your orders and see your previous purchases here.</p></div>
  </div>
  <div class="menu-item">
    <svg width="12" height="14" viewBox="0 0 12 14" fill="none" stroke="currentColor"><path d="M6 1.5 7.5 5h3.5L8.2 7.3l1 3.7L6 8.9 2.8 11l1-3.7L1 5h3.5Z"/></svg>
    <div><h4>Favorite stores</h4><p>Save the stores you visit most.</p></div>
  </div>
</aside>

<main class="account-panel">
  <h1 class="panel-title">Access your account</h1>

  <section class="block">
    <div class="field-row"><span class="field-label">Password</span><a class="field-action">Password change</a></div>
    <p>If you want to change your password, click on "Change password" and enter the required information.</p>
  </section>
  <hr class="divider">

  <section class="block">
    <div class="field-row"><span class="field-label">Your email address</span><a class="field-action">CHANGE EMAIL</a></div>
    <p>info@lunestudio.com</p>
    <div class="sub-label">Newsletter</div>
    <p>Sign up for the Newsletter and you will receive the latest news, information about promotions and discounts on lune.com</p>
    <p>I have read the Privacy Policy and would like to receive personalised business news and communications from LUNE via email and other means.</p>
    <div class="choices">
      <span class="choice"><span class="box"></span>Activate</span>
      <span class="choice"><span class="box"></span>Deactivate</span>
    </div>
  </section>
  <hr class="divider">

  <section class="block">
    <h2 class="section-title">Personal data</h2>
    <p>At LUNE we take your privacy seriously and are committed to protecting your personal information. The Privacy Policy below shows how we protect and use your data.</p>
    <p class="strong">You will be able to access and modify personal data (name, billing address, phone...)</p>
  </section>
  <hr class="divider solid">

  <section class="block billing">
    <div class="field-row"><span class="field-label">Billing data</span><a class="field-action">Password change</a></div>
    <p class="strong">Ada Marlow</p>
    <p>info@lunestudio.com</p>
    <p style="margin-top:10px">Romania</p>
    <p>Mobile phone: +40</p>
  </section>
  <hr class="divider">

  <section class="block">
    <h2 class="section-title">My addresses</h2>
    <p>ADD A NEW ADDRESS</p>
  </section>
  <hr class="divider">

  <section class="block">
    <h2 class="section-title">Favorite stores</h2>
    <p>Here you will be able to save the addresses of your favorite LUNE stores which will facilitate the online shopping process.</p>
    <div class="sub-label">ADD A NEW STORE</div>
    <div class="store-form">
      <div class="input county"><span>Romania</span><span>▾</span></div>
      <div class="input city"><span>Location</span></div>
      <div class="search-btn">SEARCH</div>
    </div>
  </section>
</main>

<footer class="site-footer">
  <div class="footer-brand"><span class="brand-name">LUNE</span></div>
  <div class="footer-col col-help">
    <h5>HELP</h5>
    <ul><li>Terms &amp; Conditions</li><li>Privacy Policy</li><li>Returns/exchanges</li><li>Delivery information</li><li>FAQ</li></ul>
  </div>
  <div class="footer-col col-shop">
    <h5>SHOP</h5>
    <ul><li>Tops</li><li>Bottoms</li><li>Intimates</li><li>Dresses</li><li>Swim</li></ul>
  </div>
  <div class="footer-col col-contact">
    <h5>CONTACT US</h5>
    <ul><li>✉ info@lunestudio.com</li></ul>
    <h5 style="margin-top:8px">FOLLOW US</h5>
    <div class="socials"><span></span><span></span><span></span><span></span><span></span></div>
  </div>
  <div class="footer-base">Terms &amp; Conditions, Privacy Policy and © 2020 LUNE</div>
</footer>

</body>
</html>
```